New Business Card Design Project LORVANTI-Italy

we are LORVANTI-Italy
our company in the market for 3 years we are luxury cosmetic company and its about time for a facelift :)
i will like to have elegant luxurious and unique business card
that will give the person that get it a unique, luxurious and elegant impression
I'm VERY OPEN FOR NEW IDEAS , even duo i add a few files of things that i see on line and i like them

i add my logo as well
my website is LORVANTI.COM
(if you would like to see the main style that we have)

Target Market(s)

adult that have money :)

Industry/Entity Type

Business

Contact Information for Business Card

Name - Dario Lorvanti
Position - CEO and CO Founder
address - 4817 E Halvern
telephone - 555-384-1926
email - dario@lorvanti.com
fax - 555-384-1926
website - LORVANTI.COM

Colors
000000
959595
fbee3e
ffffff

Requirements
Must have
• big logo in GOLD color
• elegant look
• impressive
Nice to have
• not must but maybe classy pattern background
• not must but maybe emblem
• maybe clear plastic business card
Should not have
• colors
• images

```html
<!DOCTYPE html>
<html lang="en">
<head>
<meta charset="utf-8">
<title>LORVANTI – Business Card</title>
<link href="https://fonts.googleapis.com/css2?family=Roboto:wght@400;700&display=swap" rel="stylesheet">
<style>
  :root {
    --stage: #2b2622;
    --card: #16181b;
    --card-edge: #222528;
    --gold: #d4a92a;
    --white: #f2f2f2;
    --grey: #959595;
  }
  * { box-sizing: border-box; margin: 0; padding: 0; }
  html, body { width: 1200px; height: 769px; overflow: hidden; }
  body {
    background: var(--stage);
    font-family: "Roboto", sans-serif;
    display: flex;
    align-items: center;
    justify-content: center;
    gap: 70px;
  }
  .card {
    background: var(--card);
    border: 1px solid var(--card-edge);
    box-shadow: 0 18px 40px rgba(0,0,0,.45);
  }
  .brand-mark {
    display: flex;
    flex-direction: column;
    align-items: center;
    color: var(--gold);
  }
  .brand-mark .ring {
    border: 3px solid currentColor;
    border-radius: 50%;
  }
  .brand-mark .name {
    font-weight: 400;
    letter-spacing: 6px;
    line-height: 1;
  }
  /* Contact side – portrait */
  .card-contact {
    width: 320px;
    height: 560px;
    display: flex;
    flex-direction: column;
    align-items: center;
    padding-top: 52px;
    text-align: center;
  }
  .card-contact .brand-mark { margin-bottom: 46px; }
  .card-contact .ring { width: 96px; height: 96px; margin-bottom: 14px; }
  .card-contact .name { font-size: 18px; }
  .person-name {
    color: var(--gold);
    font-weight: 700;
    font-size: 22px;
    letter-spacing: .5px;
    text-transform: uppercase;
  }
  .person-role { color: var(--white); font-size: 15px; margin-top: 6px; }
  .rule { width: 26px; height: 2px; background: var(--gold); margin: 16px 0; }
  .detail { color: var(--white); font-size: 15px; line-height: 1.7; }
  .detail .label { color: var(--gold); font-weight: 700; }
  .website { color: var(--gold); font-size: 15px; margin-top: 40px; letter-spacing: .5px; }
  /* Brand side – landscape */
  .card-brand {
    width: 560px;
    height: 320px;
    display: flex;
    flex-direction: column;
    align-items: center;
    justify-content: center;
  }
  .card-brand .ring { width: 104px; height: 104px; margin-bottom: 22px; }
  .card-brand .name { font-size: 42px; }
  .brand-country {
    color: var(--grey);
    font-size: 13px;
    letter-spacing: 5px;
    margin-top: 12px;
    padding-top: 10px;
    border-top: 1px solid var(--grey);
    width: 250px;
    text-align: center;
  }
</style>
</head>
<body>
  <section class="card card-contact">
    <div class="brand-mark"><span class="ring"></span><span class="name">LORVANTI</span></div>
    <h1 class="person-name">Dario Lorvanti</h1>
    <p class="person-role">CEO &amp; CO Founder</p>
    <div class="rule"></div>
    <p class="detail">4817 E Halvern</p>
    <div class="rule"></div>
    <p class="detail"><span class="label">P:</span> 555-384-1926 <span class="label">F:</span> 555-384-1926</p>
    <p class="detail"><span class="label">E:</span> dario@lorvanti.com</p>
    <p class="website">WWW.LORVANTI.COM</p>
  </section>

  <section class="card card-brand">
    <div class="brand-mark"><span class="ring"></span><span class="name">LORVANTI</span></div>
    <p class="brand-country">ITALY</p>
  </section>
</body>
</html>
```